Business Card: RW Office Partners - Your organised problem solver

Business Name: RW Office Partners
Website: www.rwofficepartners.com.au
Email: marisol@rwofficepartners.com.au
Mobile: 61 482 907 236
Facebook: @rwofficepartners
Instrgram: @rwofficepartners

Brading Colours:
HEX
#986474
#ddccd3
#7a8498
#c9d8e4
#000000
#ffffff

Tag Line: Your organised problem solver

Link to DRAFT website:
https://deskhelpcollective.wixsite.com/rw-office-partners

About Page from the website:
My name is Marisol Wrenfield, and I would love to assist you to become more productive in your day to day and achieve your business and personal goals.
My mission is to give you time, time to work on the important tasks of your business or to be able to spend more time with your family. I will take on the tasks you don’t have time for, don’t know well or simply don’t like to do.
I have an extensive background in Administration, Tender Coordination, Document Control, WHS and Quality Management working primarily in the Construction, Mining and Corporate World.
I am passionate about being organised, having order and making things in your life (and mine) easier! I love to watch something unfold and grow into something amazing! I am known for being the go-to problem solver, the organiser of all things, producing high standards of work even under pressure. I’m also a confident communicator, and I understand that you’re busy running your business.

Target Market(s)

Small to Medium Business who require assistance in their business by a virtual assistant.

Industry/Entity Type

Virtual Assistant

Contact Information for Business Card

Mobile: 61 482 907 236

Font styles to use
Sans Serif

Colors
ffffff

Requirements
Must have
• Branding Colours as outlined.
Contact Details as outlined.
Logo as provided.
Proper contact details - mobile, facebook, instragm, website.
Simple, Elegant, very clean looking.
Should not have
• Note cute with pictures.
Not too girly as still want to market to construction companies.

```html
<!DOCTYPE html>
<html lang="en">
<head>
<meta charset="utf-8">
<title>RW Office Partners – Business Card</title>
<link href="https://fonts.googleapis.com/css2?family=Cabin:wght@600&family=Roboto:wght@400;500&display=swap" rel="stylesheet">
<style>
  :root {
    --plum: #986474;
    --plum-soft: #ddccd3;
    --slate: #7a8498;
    --slate-soft: #c9d8e4;
    --ink: #222222;
    --paper: #ffffff;
    --backdrop: #6a6667;
  }
  * { margin: 0; padding: 0; box-sizing: border-box; }
  html, body { width: 1200px; height: 1200px; overflow: hidden; }
  body {
    background: var(--backdrop);
    font-family: "Roboto", Arial, sans-serif;
    color: var(--ink);
    position: relative;
  }
  .card {
    position: absolute;
    width: 712px;
    height: 417px;
    background: var(--paper);
    border-radius: 22px;
    overflow: hidden;
  }
  .card--front { left: 238px; top: 120px; }
  .card--back { left: 231px; top: 645px; }

  /* Wordmark */
  .wordmark {
    display: flex;
    align-items: center;
    gap: 18px;
    color: var(--slate);
    font-family: "Roboto", Arial, sans-serif;
    font-weight: 500;
    white-space: nowrap;
  }
  .wordmark__square { background: var(--plum); flex: none; }
  .card--front .wordmark {
    position: absolute;
    left: 0; right: 0; top: 150px;
    justify-content: center;
    font-size: 52px;
  }
  .card--front .wordmark__square { width: 44px; height: 44px; }

  .front-social {
    position: absolute;
    left: 0; right: 0; top: 350px;
    display: flex;
    justify-content: center;
    gap: 18px;
    font-size: 18px;
    color: #333;
  }
  .social-item { display: flex; align-items: center; gap: 10px; }
  .social-mark {
    width: 16px; height: 16px;
    border-radius: 3px;
    background: var(--plum);
    flex: none;
  }
  .brand-band {
    position: absolute;
    left: 0; right: 0; bottom: 0;
    height: 16px;
    display: flex;
  }
  .brand-band__plum { flex: 0 0 357px; background: var(--plum); }
  .brand-band__slate { flex: 1; background: var(--slate); }

  /* Back */
  .card--back .wordmark {
    position: absolute;
    left: 32px; top: 168px;
    font-size: 27px;
    gap: 10px;
  }
  .card--back .wordmark__square { width: 24px; height: 24px; }
  .tagline {
    position: absolute;
    left: 32px; top: 226px;
    font-size: 19px;
    color: #333;
  }
  .contact-block { position: absolute; left: 350px; top: 102px; }
  .person-name {
    font-family: "Cabin", Arial, sans-serif;
    font-weight: 600;
    font-size: 27px;
    color: var(--plum);
    line-height: 1.1;
  }
  .person-role { font-size: 18px; color: #333; margin-top: 6px; }
  .contact-list { list-style: none; margin-top: 22px; }
  .contact-list li {
    display: flex;
    align-items: center;
    gap: 12px;
    font-size: 18.5px;
    color: #333;
    height: 26px;
  }
  .contact-icon { width: 18px; height: 18px; flex: none; }
  .contact-list .social-mark { width: 16px; height: 16px; margin: 0 1px; }
</style>
</head>
<body>

<section class="card card--front" aria-label="Card front">
  <div class="wordmark">
    <span class="wordmark__square"></span>
    <span class="wordmark__name">RW Office Partners</span>
  </div>
  <div class="front-social">
    <span class="social-item"><span class="social-mark"></span>@rwofficepartners</span>
    <span class="social-item"><span class="social-mark"></span>@rwofficepartners</span>
  </div>
  <div class="brand-band">
    <span class="brand-band__plum"></span>
    <span class="brand-band__slate"></span>
  </div>
</section>

<section class="card card--back" aria-label="Card back">
  <div class="wordmark">
    <span class="wordmark__square"></span>
    <span class="wordmark__name">RW Office Partners</span>
  </div>
  <p class="tagline">Your organised problem solver</p>

  <div class="contact-block">
    <h1 class="person-name">Marisol Wrenfield</h1>
    <p class="person-role">Virtual Assistant</p>
    <ul class="contact-list">
      <li>
        <svg class="contact-icon" viewBox="0 0 18 18" aria-hidden="true">
          <path d="M2 6 Q9 1 16 6 L14 8 L12 6.5 L6 6.5 L4 8 Z" fill="#986474"/>
          <rect x="4" y="9" width="10" height="6" rx="1" fill="#986474"/>
          <circle cx="9" cy="12" r="1.6" fill="#fff"/>
        </svg>
        61 482 907 236
      </li>
      <li>
        <svg class="contact-icon" viewBox="0 0 18 18" aria-hidden="true">
          <rect x="1.5" y="4" width="15" height="10" fill="#986474"/>
          <path d="M1.5 4 L9 10 L16.5 4" fill="none" stroke="#fff" stroke-width="1.3"/>
        </svg>
        marisol@rwofficepartners.com.au
      </li>
      <li>
        <svg class="contact-icon" viewBox="0 0 18 18" aria-hidden="true">
          <g fill="none" stroke="#986474" stroke-width="1.3">
            <circle cx="9" cy="9" r="6.5"/>
            <ellipse cx="9" cy="9" rx="3" ry="6.5"/>
            <line x1="2.5" y1="9" x2="15.5" y2="9"/>
          </g>
        </svg>
        www.rwofficepartners.com.au
      </li>
      <li><span class="social-mark"></span>@rwofficepartners</li>
      <li><span class="social-mark"></span>@rwofficepartners</li>
    </ul>
  </div>
</section>

</body>
</html>
```